Corvana Tongue Works, LLC

We need a business card that includes information about our business and conveys a reliable business that provides document translation services and interpreters for a variety of corporate and individual clients. We want to come across as professional, reliable, yet approachable. It should include the following on one side:

ESL / ENL Language Classes, Private Lessons, and Online Tutors
PLEXA Training and Testing
Translating & Interpreting Services
Contact us about Over-the-Phone Interpreting in over 200 languages
24/7/365
www.corvanatongue.example

The other side should include (555) 481-3062

Rhoda Pelling, President
482 Garnet Ave., Ste. 219
Larkfield, WV 40917

Please add USA as part of the address. Also, please add rmpelling@corvanatongueworks.example as the e-mail address. Thank you.

Target Market(s)

Business professionals, their families, the international community

Industry/Entity Type

Business

Contact Information for Business Card

24/7/365
www.corvanatongue.example

(555) 481-3062

Rhoda Pelling, President
482 Garnet Ave., Ste. 219
Larkfield, WV 40917
USA

Font styles to use
Sans Serif

Colors

Designer to choose colors to be used in the design.

Requirements
Must have
• See project description
• e-mail address and web address
• Phone number
Nice to have
• a globe
• physical address
Should not have
• Should not have the same color scheme as other agencies in our market in Indiana unless it is blue and black. No purple or yellow.

```html
<!DOCTYPE html>
<html lang="en">
<head>
<meta charset="utf-8">
<title>Corvana Tongue Works – Business Card</title>
<link rel="stylesheet" href="https://fonts.googleapis.com/css2?family=Poppins:wght@400;500;600&display=swap">
<style>
  :root {
    --backdrop: #d4d4d4;
    --card-white: #ffffff;
    --card-black: #050505;
    --brand-blue: #2a8fd4;
    --rule-blue: #1f6fb8;
    --ink: #151515;
    --ink-soft: #333333;
    --paper-text: #ffffff;
  }
  * { box-sizing: border-box; margin: 0; padding: 0; }
  html, body {
    width: 1200px; height: 800px; overflow: hidden;
    background: var(--backdrop);
    font-family: "Poppins", sans-serif;
  }
  .sheet {
    width: 1200px; height: 800px;
    display: flex; flex-direction: column;
    align-items: center; justify-content: center; gap: 40px;
  }
  .card {
    width: 620px; height: 354px; position: relative;
    box-shadow: 0 6px 18px rgba(0,0,0,.18);
  }

  /* Front */
  .card--front { background: var(--card-white); color: var(--ink); }
  .services {
    position: absolute; top: 28px; left: 0; right: 0;
    text-align: center; font-size: 13.5px; line-height: 1.45; color: var(--ink-soft);
  }
  .services__rule {
    position: absolute; top: 38px; height: 1px; background: var(--brand-blue);
  }
  .services__rule--left { left: 0; width: 82px; }
  .services__rule--right { right: 0; width: 82px; }
  .services__line { display: block; }

  .brand {
    display: flex; align-items: center; gap: 12px;
  }
  .brand__dot {
    width: 58px; height: 58px; border-radius: 50%;
    background: var(--brand-blue); flex: none;
  }
  .brand__name {
    font-weight: 500; font-size: 21px; line-height: 1.1;
  }
  .card--front .brand {
    position: absolute; left: 50px; top: 186px;
  }
  .card--front .brand__name { color: var(--ink); }

  .divider {
    position: absolute; left: 338px; top: 150px; width: 1.5px; height: 160px;
    background: var(--rule-blue);
  }
  .contact {
    position: absolute; left: 364px; top: 150px; font-size: 12.5px; line-height: 1.5;
    color: var(--ink);
  }
  .contact__name {
    color: var(--brand-blue); font-weight: 500; font-size: 22px;
    letter-spacing: .5px; text-transform: uppercase; line-height: 1.1;
  }
  .contact__title { font-size: 12.5px; margin-bottom: 10px; }
  .contact__address { margin-bottom: 6px; }
  .contact__row { display: flex; align-items: center; gap: 8px; }
  .contact__icon { width: 10px; height: 10px; flex: none; }

  /* Back */
  .card--back {
    background: var(--card-black); color: var(--paper-text);
    display: flex; flex-direction: column; align-items: center; justify-content: center;
  }
  .card--back .brand__dot { width: 92px; height: 92px; }
  .card--back .brand__name { color: var(--paper-text); font-size: 30px; }
  .card--back .brand { margin-bottom: 34px; }
  .hotline { text-align: center; font-size: 14px; line-height: 1.5; }
</style>
</head>
<body>
<main class="sheet">

  <section class="card card--front" aria-label="Business card front">
    <span class="services__rule services__rule--left"></span>
    <span class="services__rule services__rule--right"></span>
    <p class="services">
      <span class="services__line">ESL / ENL Language Classes, Private Lessons, and Online Tutors</span>
      <span class="services__line">PLEXA Training and Testing</span>
      <span class="services__line">Translating &amp; Interpreting Services</span>
    </p>

    <div class="brand">
      <span class="brand__dot"></span>
      <p class="brand__name">Corvana<br>Tongue<br>Works LLC</p>
    </div>

    <span class="divider"></span>

    <div class="contact">
      <p class="contact__name">Rhoda Pelling</p>
      <p class="contact__title">President</p>
      <p class="contact__address">482 Garnet Ave., Ste. 219<br>Larkfield, WV 40917 USA</p>
      <p class="contact__row">
        <svg class="contact__icon" viewBox="0 0 10 10" aria-hidden="true"><path d="M2 0.5 L3.6 2.6 L2.7 3.6 Q3.8 5.9 6.3 7.2 L7.4 6.3 L9.5 7.9 L8.3 9.5 Q1.5 8 0.5 1.5 Z" fill="var(--brand-blue)"/></svg>
        (555) 481-3062
      </p>
      <p class="contact__row">
        <svg class="contact__icon" viewBox="0 0 10 10" aria-hidden="true"><rect x="0.5" y="2" width="9" height="6.5" fill="var(--brand-blue)"/><path d="M0.8 2.3 L5 5.6 L9.2 2.3" stroke="#fff" stroke-width="0.9" fill="none"/></svg>
        info@corvanatongue.example
      </p>
      <p class="contact__row">
        <svg class="contact__icon" viewBox="0 0 10 10" aria-hidden="true"><circle cx="5" cy="5" r="4.5" fill="var(--brand-blue)"/><path d="M0.5 5 H9.5 M5 0.5 Q2.5 5 5 9.5 M5 0.5 Q7.5 5 5 9.5" stroke="#fff" stroke-width="0.7" fill="none"/></svg>
        www.corvanatongue.example
      </p>
    </div>
  </section>

  <section class="card card--back" aria-label="Business card back">
    <div class="brand">
      <span class="brand__dot"></span>
      <p class="brand__name">Corvana<br>Tongue<br>Works LLC</p>
    </div>
    <p class="hotline">
      Contact us about Over-the-Phone Interpreting in over 200 languages<br>
      24/7/365
    </p>
  </section>

</main>
</body>
</html>
```